Manifesto

I want a manifesto with the following five manifestos for our Not for Profit

- We are a For-purpose organisation
- Every service we offer is free
- Every product we sell funds our services
- Every financial transaction is transparent
- Our service is for the greater good
- Our purpose is always to serve the people
- We are a for purpose organisation

Its to go with this website logo/look/feel www.brightharbour.co.nz

Two attachments:

1. I quite like this look/feel of a manifesto (see attached), I want something clean, professional but I also quite like either Retro modern look feel also like a fresh, and uplifting as its for sick people coming to see us and our funds where anyone buys a product are used for helping those who are sick with healing......so needs something conveyed that is fresh, uplifing yet professional.
2. This attachment is how I wrote this down when inspired of how I wanted Bright Harbour to operate. This is our values chart. It has to say

Also check out our website for our logo, look etc.. it doesnt have to be the same but red somewhere would link back to logo. www.brightharbour.co.nz .

Industry/Entity Type

Financial

```html
<!DOCTYPE html>
<html lang="en">
<head>
<meta charset="utf-8">
<title>Bright Harbour Manifesto</title>
<link rel="stylesheet" href="https://fonts.googleapis.com/css2?family=Archivo+Black&family=Arvo:wght@400;700&family=Josefin+Sans:wght@700&family=Lobster&family=Lobster+Two:ital,wght@1,700&family=Roboto+Slab:wght@500&display=swap">
<style>
  :root {
    --backdrop: #2e2e2e;
    --paper: #ececec;
    --paper-edge: #dcdcdc;
    --ink: #3b3b3b;
    --red: #c3172b;
    --red-shadow: rgba(90, 0, 10, 0.35);
  }
  * { margin: 0; padding: 0; box-sizing: border-box; }
  html, body {
    width: 1200px; height: 1000px; overflow: hidden;
    background: var(--backdrop);
  }
  .poster {
    position: absolute; left: 266px; top: 20px;
    width: 620px; height: 890px;
    transform: scale(1.078); transform-origin: top left;
    background: radial-gradient(ellipse at 50% 40%, #f3f3f3 0%, var(--paper) 55%, var(--paper-edge) 100%);
    color: var(--ink);
  }
  .poster > * { position: absolute; white-space: nowrap; line-height: 1; }
  .red { color: var(--red); text-shadow: 1px 2px 2px var(--red-shadow); }
  .script { font-family: "Lobster", cursive; font-weight: 400; }
  .slab { font-family: "Arvo", serif; font-weight: 700; }
  .heavy { font-family: "Archivo Black", sans-serif; }
  .caps { font-family: "Josefin Sans", sans-serif; font-weight: 700; }

  .title { left: 0; width: 620px; top: 36px; text-align: center;
    font-family: "Lobster Two", cursive; font-style: italic; font-weight: 700; font-size: 30px; }

  .lead-we { left: 20px; top: 92px; font-size: 55px; }
  .lead-purpose { left: 20px; top: 148px; font-size: 38px; letter-spacing: -0.5px; }
  .lead-org { left: 20px; top: 193px; font-size: 33px; letter-spacing: -0.5px; }

  .free-intro { left: 374px; top: 96px; width: 232px; text-align: center; font-size: 38px; }
  .free-mid { left: 374px; top: 139px; width: 232px; text-align: center;
    font-family: "Roboto Slab", serif; font-weight: 500; font-size: 21px; letter-spacing: 6px; }
  .free-word { left: 374px; top: 160px; width: 232px; text-align: center; font-size: 80px; letter-spacing: 4px; }

  .rule { left: 52px; width: 520px; height: 6px; }
  .rule-1 { top: 242px; } .rule-2 { top: 365px; } .rule-3 { top: 554px; } .rule-4 { top: 689px; }

  .product-head { left: 0; width: 620px; text-align: center; top: 266px; font-size: 53px; }
  .product-sub { left: 0; width: 620px; text-align: center; top: 320px; font-family: "Arvo", serif; font-size: 29px; font-weight: 700; }

  .fin-every { left: 22px; top: 388px; font-size: 57px; letter-spacing: 12px; }
  .fin-financial { left: 22px; top: 444px; font-size: 30px; letter-spacing: 5px; }
  .fin-transaction { left: 22px; top: 482px; font-family: "Roboto Slab", serif; font-weight: 500; font-size: 24px; letter-spacing: 4.5px; }
  .fin-transparent { left: 22px; top: 508px; font-family: "Roboto Slab", serif; font-weight: 500; font-size: 23px; letter-spacing: 3.5px; }

  .good-intro { left: 330px; width: 276px; text-align: center; top: 392px; font-size: 27px; letter-spacing: 2.5px; }
  .good-mid { left: 330px; width: 276px; text-align: center; top: 416px; font-size: 43px; }
  .good-word { left: 330px; width: 276px; text-align: center; top: 466px; font-size: 72px; letter-spacing: 1px; }

  .people-head { left: 0; width: 620px; text-align: center; top: 580px; font-size: 47px; letter-spacing: 3px; }
  .people-sub { left: 0; width: 620px; text-align: center; top: 620px; font-size: 45px; }

  .close-head { left: 0; width: 620px; text-align: center; top: 720px; font-size: 41px; letter-spacing: 1.5px; }
  .close-word { left: 0; width: 620px; text-align: center; top: 752px; font-size: 92px; }

  .site { left: 0; width: 620px; text-align: center; top: 859px;
    font-family: "Josefin Sans", sans-serif; font-weight: 700; font-size: 11px; letter-spacing: 2px; }
</style>
</head>
<body>
  <main class="poster">
    <h1 class="title">Bright Harbour Manifesto</h1>

    <p class="lead-we slab">WE ARE A</p>
    <p class="lead-purpose heavy red">FOR PURPOSE</p>
    <p class="lead-org heavy red">ORGANISATION</p>

    <p class="free-intro script red">Every Service</p>
    <p class="free-mid">we offer is</p>
    <p class="free-word slab">FREE</p>

    <svg class="rule rule-1" viewBox="0 0 520 6" preserveAspectRatio="none" aria-hidden="true"><path d="M0 3 Q260 0 520 3 Q260 6 0 3Z" fill="var(--ink)"/></svg>

    <p class="product-head slab red">EVERY PRODUCT</p>
    <p class="product-sub">we sell funds our services</p>

    <svg class="rule rule-2" viewBox="0 0 520 6" preserveAspectRatio="none" aria-hidden="true"><path d="M0 3 Q260 0 520 3 Q260 6 0 3Z" fill="var(--ink)"/></svg>

    <p class="fin-every slab red">EVERY</p>
    <p class="fin-financial slab red">FINANCIAL</p>
    <p class="fin-transaction">TRANSACTION</p>
    <p class="fin-transparent">is transparent</p>

    <p class="good-intro caps">OUR SERVICE IS</p>
    <p class="good-mid script red">for the greater</p>
    <p class="good-word heavy red">GOOD</p>

    <svg class="rule rule-3" viewBox="0 0 520 6" preserveAspectRatio="none" aria-hidden="true"><path d="M0 3 Q260 0 520 3 Q260 6 0 3Z" fill="var(--ink)"/></svg>

    <p class="people-head caps">OUR PURPOSE IS</p>
    <p class="people-sub script red">always to serve the people</p>

    <svg class="rule rule-4" viewBox="0 0 520 6" preserveAspectRatio="none" aria-hidden="true"><path d="M0 3 Q260 0 520 3 Q260 6 0 3Z" fill="var(--ink)"/></svg>

    <p class="close-head caps">WE ARE A FOR PURPOSE</p>
    <p class="close-word script red">organisation</p>

    <p class="site">www.brightharbour.co.nz</p>
  </main>
</body>
</html>
```